SkyvornQ Business Cards and Stationary Design

Need a design for our business cards and stationary. I want to carry on the theme of the logo. I want the business cards to have a design on the back. I would like the business cards and the stationary to carry the same theme, design scheme, and branding

Target Market(s)

Airlines and Maintenance Facilities

Industry/Entity Type

Aviation

Contact Information for Business Card

Name
Position Title
Address: 4827 Trellis Hollow Road, Fort Pierce, Florida, 34951
Office Number
Mobile Number
Email
Website

Font styles to use
Serif
Sans Serif

Colors

Designer to choose colors to be used in the design.

```html
<!DOCTYPE html>
<html lang="en">
<head>
<meta charset="utf-8">
<title>SkyvornQ Business Card</title>
<link href="https://fonts.googleapis.com/css2?family=Roboto:wght@400;500;700&display=swap" rel="stylesheet">
<style>
  :root {
    --backdrop: #2b2b2d;
    --card-white: #f2f2f2;
    --navy: #0d2452;
    --blue-deep: #0b3a80;
    --blue-mid: #0a62b8;
    --blue-bright: #0aa2e8;
    --text-grey: #4a4a4a;
    --white: #ffffff;
  }
  * { margin: 0; padding: 0; box-sizing: border-box; }
  html, body { width: 1200px; height: 960px; overflow: hidden; }
  body {
    background: var(--backdrop);
    font-family: "Roboto", Arial, sans-serif;
    position: relative;
  }
  .card {
    position: absolute;
    width: 600px;
    height: 343px;
    border-radius: 20px;
    overflow: hidden;
  }
  .card-front { left: 314px; top: 113px; background: var(--card-white); }
  .card-back {
    left: 311px; top: 472px;
    background: radial-gradient(ellipse 60% 70% at 50% 45%, var(--blue-bright) 0%, var(--blue-mid) 55%, var(--blue-deep) 100%);
  }

  .brand { position: absolute; left: 44px; top: 32px; width: 224px; height: 110px; }
  .brand-mark {
    position: absolute; left: 124px; top: 0;
    width: 68px; height: 68px; border-radius: 50%;
    border: 6px solid var(--blue-mid);
  }
  .brand-name {
    position: absolute; left: 0; bottom: 0; width: 224px;
    font-size: 27px; font-weight: 700; letter-spacing: 3px;
    color: var(--navy); text-align: center;
  }

  .name-band {
    position: absolute; right: 0; top: 89px;
    width: 234px; height: 53px;
    background: linear-gradient(90deg, var(--blue-deep), var(--blue-mid) 50%, var(--blue-bright));
    clip-path: polygon(40px 0, 100% 0, 100% 100%, 0 100%);
    color: var(--white); text-align: right; padding-right: 34px; padding-top: 5px;
  }
  .person-name { font-size: 21px; font-weight: 700; line-height: 24px; }
  .person-title { font-size: 15px; font-weight: 500; line-height: 18px; }

  .contact-list { position: absolute; right: 26px; top: 190px; list-style: none; }
  .contact-list li {
    display: flex; align-items: center; justify-content: flex-end;
    height: 19.5px; font-size: 14px; color: var(--text-grey);
  }
  .contact-list svg { width: 14px; height: 14px; margin-left: 10px; fill: var(--navy); }

  .address-band {
    position: absolute; left: 0; top: 282px; width: 100%; height: 30px;
    background: var(--navy); color: var(--white);
    display: flex; align-items: center; justify-content: flex-end;
    padding-right: 28px; font-size: 14px;
  }
  .address-band svg { width: 14px; height: 16px; margin-left: 10px; fill: var(--white); }

  .back-mark {
    position: absolute; left: 213px; top: 76px;
    width: 174px; height: 174px; border-radius: 50%;
    border: 12px solid var(--white);
    display: flex; align-items: center; justify-content: center;
  }
  .back-name { font-size: 22px; font-weight: 700; letter-spacing: 2px; color: var(--white); }
  .back-web {
    position: absolute; left: 0; top: 289px; width: 100%;
    text-align: center; font-size: 14px; letter-spacing: 5px; color: var(--white);
  }
</style>
</head>
<body>
  <section class="card card-front">
    <div class="brand">
      <div class="brand-mark"></div>
      <div class="brand-name">SKYVORNQ</div>
    </div>

    <div class="name-band">
      <div class="person-name">DANIEL REEVES</div>
      <div class="person-title">CEO/FOUNDER</div>
    </div>

    <ul class="contact-list">
      <li>689 502 7714
        <svg viewBox="0 0 24 24"><path d="M6.6 10.8a15 15 0 0 0 6.6 6.6l2.2-2.2a1 1 0 0 1 1-.25 11.4 11.4 0 0 0 3.6.57 1 1 0 0 1 1 1V20a1 1 0 0 1-1 1A17 17 0 0 1 3 4a1 1 0 0 1 1-1h3.5a1 1 0 0 1 1 1c0 1.25.2 2.45.57 3.57a1 1 0 0 1-.25 1z"/></svg></li>
      <li>836 219 4086
        <svg viewBox="0 0 24 24"><path d="M7 1h10a2 2 0 0 1 2 2v18a2 2 0 0 1-2 2H7a2 2 0 0 1-2-2V3a2 2 0 0 1 2-2zm0 3v14h10V4zm5 15.5a1.2 1.2 0 1 0 0 2.4 1.2 1.2 0 0 0 0-2.4z"/></svg></li>
      <li>info@skyvornq.com
        <svg viewBox="0 0 24 24"><path d="M2 5h20v14H2zm2 2v.4l8 5 8-5V7zm0 2.8V17h16V9.8l-8 5z"/></svg></li>
      <li>www.skyvornq.com
        <svg viewBox="0 0 24 24"><circle cx="12" cy="12" r="10"/></svg></li>
    </ul>

    <div class="address-band">4827 Trellis Hollow Road, Fort Pierce, Florida, 34951
      <svg viewBox="0 0 24 28"><path d="M12 0a9 9 0 0 0-9 9c0 7 9 19 9 19s9-12 9-19a9 9 0 0 0-9-9zm0 12.5A3.5 3.5 0 1 1 12 5.5a3.5 3.5 0 0 1 0 7z"/></svg>
    </div>
  </section>

  <section class="card card-back">
    <div class="back-mark"><span class="back-name">SKYVORNQ</span></div>
    <div class="back-web">www.skyvornq.com</div>
  </section>
</body>
</html>
```